Red Mesa Greenworks Summit needs a marketing flyer

We need a full page graphic for our upcoming Forum that can also be converted into a website "header" for social media, etc.: "Red Mesa Greenworks Summit - Shaping Change Across the Made Landscape"

INTRODUCTION:
During the first week of August 2022, Q-VarDT is presenting the Red Mesa Greenworks Summit - Shaping Change Across the Made Landscape.

One of the most exciting aspects of this conference will be the bringing together of multiple organizations including for-profits and nonprofits, K-12’s and higher education, cities and counties and other governmental agencies, as well as architects, engineers, and contractors to collaboratively present and discuss issues and ideas related to sustainability, with a Texas focus.

This event will be a catalyst for public and private project owners to holistically gather information and momentum as we bring the resources and vision needed to achieve the goal of zero carbon emissions from the built environment by 2040, and address water, green space and the natural environment, transportation, equity, and funding, among other topics.

```html
<!DOCTYPE html>
<html lang="en">
<head>
<meta charset="utf-8">
<title>Red Mesa Greenworks Summit – Header</title>
<link href="https://fonts.googleapis.com/css2?family=Montserrat:wght@300;400;600;700&display=swap" rel="stylesheet">
<style>
  :root {
    --stage: #8a8a8a;
    --paper: #f1f2f2;
    --ink: #3a3a3a;
    --green: #8bb43c;
    --blue: #0d4fa0;
    --map: #e4e5e5;
  }
  * { margin: 0; padding: 0; box-sizing: border-box; }
  html, body { width: 1200px; height: 547px; overflow: hidden; }
  body {
    background: var(--stage);
    font-family: "Montserrat", Arial, sans-serif;
    position: relative;
  }
  .header-banner {
    position: absolute;
    left: 89px; top: 66px;
    width: 1024px; height: 390px;
    background: var(--paper);
    overflow: hidden;
  }
  .banner-shapes { position: absolute; inset: 0; }
  .brand-name {
    position: absolute; left: 31px; top: 40px;
    font-weight: 300; font-size: 22px; color: var(--ink);
    letter-spacing: 3px; text-transform: uppercase;
  }
  .headline {
    position: absolute; left: 30px; top: 118px; width: 580px;
    font-weight: inherit;
  }
  .headline-event {
    display: block;
    font-weight: 300; font-size: 27px; color: var(--ink);
    letter-spacing: 0.4px; line-height: 36px; white-space: nowrap;
  }
  .headline-theme {
    display: block;
    font-weight: 700; font-size: 34px; color: var(--green);
    line-height: 44px; letter-spacing: 0.3px; margin-top: 2px;
  }
  .accent-rule {
    position: absolute; left: 31px; top: 264px;
    width: 60px; height: 3px; background: var(--blue);
  }
  .social {
    position: absolute; left: 24px; top: 333px;
    display: flex; gap: 7px;
  }
  .social-dot {
    width: 20px; height: 20px; border-radius: 50%;
    background: #fff;
  }
  .social-dot.web { background: var(--green); border: 2px solid #fff; }
  .web-address {
    position: absolute; left: 146px; top: 343px;
    font-weight: 600; font-size: 15px; color: #222;
  }
</style>
</head>
<body>
  <section class="header-banner">
    <svg class="banner-shapes" width="1024" height="390" viewBox="0 0 1024 390">
      <defs>
        <linearGradient id="photoTone" x1="0" y1="0" x2="1" y2="1">
          <stop offset="0" stop-color="#6dae4a"/>
          <stop offset="0.55" stop-color="#4f8f3a"/>
          <stop offset="1" stop-color="#2f4a2c"/>
        </linearGradient>
      </defs>
      <rect class="state-silhouette" x="320" y="15" width="220" height="270" rx="30" fill="var(--map)" role="img" aria-label="Faint state map silhouette"/>
      <polygon class="top-triangle" points="588,0 690,0 636,96" fill="var(--blue)"/>
      <polygon class="chevron-frame" points="672,0 1024,0 1024,390 682,390 590,195" fill="var(--green)"/>
      <polygon class="event-photo" points="700,0 1024,0 1024,390 712,390 616,195" fill="url(#photoTone)" role="img" aria-label="Photo of professionals in conversation over a city skyline, green toned"/>
      <polygon class="bottom-band" points="0,327 665,327 685,363 0,363" fill="var(--blue)"/>
      <polygon class="address-tab" points="110,316 382,316 412,390 140,390" fill="var(--green)"/>
    </svg>

    <p class="brand-name">Q-VarDT</p>

    <h1 class="headline">
      <span class="headline-event">RED MESA GREENWORKS SUMMIT</span>
      <span class="headline-theme">- SHAPING CHANGE ACROSS THE MADE LANDSCAPE</span>
    </h1>
    <div class="accent-rule"></div>

    <div class="social">
      <span class="social-dot"></span>
      <span class="social-dot web"></span>
      <span class="social-dot"></span>
    </div>
    <p class="web-address">www.q-vardt.example.org</p>
  </section>
</body>
</html>
```